business card deign

Logo needs the following on it.
1. attached logo
2. Tagline - "If it chills your cooler or lifts the crowd...we bring it!"
3. Name- Dalton Pikes, Founder and CPO
4. Address - 412 E. Carver Avenue, Ste 2207, Tampa, FL. 33917
5. Phone - 555.318.4726

```html
<!DOCTYPE html>
<html lang="en">
<head>
<meta charset="utf-8">
<title>Brimwell Business Card</title>
<link href="https://fonts.googleapis.com/css2?family=Roboto:wght@400;500;700&display=swap" rel="stylesheet">
<style>
  :root {
    --backdrop: #e6d2bc;
    --card: #ffffff;
    --ink: #0d0d0d;
    --ink-soft: #333333;
    --emboss: #f1f1f1;
    --shadow: rgba(70, 45, 25, 0.28);
  }
  * { box-sizing: border-box; margin: 0; padding: 0; }
  html, body {
    width: 1200px; height: 711px; overflow: hidden;
    background: var(--backdrop);
    font-family: "Roboto", Arial, sans-serif;
    color: var(--ink);
  }
  .stage {
    position: relative; width: 1200px; height: 711px;
    display: flex; align-items: center; justify-content: center; gap: 48px;
  }
  .card {
    position: relative; width: 532px; height: 304px;
    background: var(--card);
    box-shadow: 0 14px 30px var(--shadow);
    overflow: hidden;
  }
  .emboss-art {
    position: absolute;
    background: radial-gradient(ellipse at center, var(--emboss) 0%, rgba(241,241,241,0.4) 60%, rgba(255,255,255,0) 75%);
  }
  .card-back .emboss-art { left: 120px; top: 10px; width: 300px; height: 290px; }
  .card-front .emboss-art { right: -10px; top: 60px; width: 230px; height: 240px; }

  .wordmark {
    font-weight: 700; letter-spacing: 0; color: var(--ink);
  }
  .card-back .wordmark {
    position: absolute; right: 28px; bottom: 26px; font-size: 28px;
  }

  .holder {
    position: absolute; top: 26px; right: 0;
    display: flex; align-items: flex-start; gap: 14px;
  }
  .holder-text { text-align: right; padding-top: 2px; }
  .holder-name { font-size: 30px; font-weight: 700; line-height: 1; }
  .holder-title { font-size: 15px; font-weight: 500; margin-top: 6px; }
  .holder-bar { width: 34px; height: 40px; background: var(--ink); }

  .brand-block { position: absolute; left: 34px; top: 128px; }
  .card-front .wordmark { font-size: 34px; line-height: 1; display: flex; align-items: center; gap: 12px; }
  .brand-dot { width: 16px; height: 16px; border-radius: 50%; background: var(--ink); }
  .tagline {
    font-size: 14px; font-weight: 500; line-height: 1.35; margin-top: 14px; color: var(--ink-soft);
    max-width: 250px;
  }
  .contact { margin-top: 10px; font-size: 14px; font-weight: 500; line-height: 1.4; }
  .contact-row { display: flex; align-items: flex-start; gap: 8px; }
  .contact-row svg { width: 14px; height: 14px; margin-top: 2px; flex: none; }
</style>
</head>
<body>
<main class="stage">
  <section class="card card-back" aria-label="Card back">
    <div class="emboss-art" role="img" aria-label="Faint embossed leaping animal silhouette"></div>
    <div class="wordmark">Brimwell</div>
  </section>

  <section class="card card-front" aria-label="Card front">
    <div class="emboss-art" role="img" aria-label="Faint embossed leaping animal silhouette"></div>
    <div class="holder">
      <div class="holder-text">
        <div class="holder-name">Dalton Pikes</div>
        <div class="holder-title">Founder and CPO</div>
      </div>
      <div class="holder-bar"></div>
    </div>
    <div class="brand-block">
      <div class="wordmark"><span class="brand-dot"></span>Brimwell</div>
      <p class="tagline">If it chills your cooler or lifts the crowd...we bring it!</p>
      <div class="contact">
        <div class="contact-row">
          <svg viewBox="0 0 24 24" aria-hidden="true"><path fill="currentColor" d="M6.6 10.8a15.1 15.1 0 0 0 6.6 6.6l2.2-2.2a1 1 0 0 1 1-.25 11.4 11.4 0 0 0 3.6.57 1 1 0 0 1 1 1V20a1 1 0 0 1-1 1A17 17 0 0 1 3 4a1 1 0 0 1 1-1h3.5a1 1 0 0 1 1 1c0 1.25.2 2.45.57 3.57a1 1 0 0 1-.25 1z"/></svg>
          <span>555.318.4726</span>
        </div>
        <div class="contact-row">
          <svg viewBox="0 0 24 24" aria-hidden="true"><path fill="currentColor" d="M12 2a7 7 0 0 0-7 7c0 5.2 7 13 7 13s7-7.8 7-13a7 7 0 0 0-7-7zm0 9.5A2.5 2.5 0 1 1 12 6.5a2.5 2.5 0 0 1 0 5z"/></svg>
          <span>412 E. Carver Avenue,<br>Ste 2207, Tampa, FL. 33917</span>
        </div>
      </div>
    </div>
  </section>
</main>
</body>
</html>
```